Website Banner Redesign for Kelvra Cargo Depot

Business Name:
KELVRA CARGO DEPOT

About Us:
- We’re a proudly Australian company that designs and builds tough, reliable toolboxes for Utes, Trucks, and Campervans. Our products are made to handle harsh conditions and are trusted by tradies, off-roaders, and professional fleets across the country.

Project Goal:
- We want to refresh our homepage and category banners with bold, modern designs that better showcase our products and value proposition.

Why We’re Updating:
Our current banners show the products well, but we want to improve:
Visual impact and hierarchy
- Readability of text (especially on mobile)
- Clearer calls-to-action (CTAs)
- Brand messaging around “Built Tough”, “Aussie Made”, and “Custom Fit-Outs”

Target Audience:
- Tradespeople
- 4x4 & off-road enthusiasts
- Caravan & camping community
- Ute/Truck/Caravan dealerships
- Fleet and commercial buyers

Design Style We Want:
- Bold, confident, rugged
- Clean layout with clear focal points
- Strong product imagery (we’ll supply photos)
- Use of brand colors: Black, White, Red, Grey
- Professional, not too busy or cluttered

Banner Uses:
- Homepage hero banner
- Category landing pages

UTE TOOLBOXES - https://www.kelvracargo.com.au/aluminium-toolboxes/
Truck Boxes - https://www.kelvracargo.com.au/truck-toolboxes/
Canopies - https://www.kelvracargo.com.au/canopy/
Dog Boxes - https://www.kelvracargo.com.au/dog-boxes/
CAMPER BOXES - https://www.kelvracargo.com.au/camper-toolboxes/
Accessories - https://www.kelvracargo.com.au/accessories/

- Can be reused for desktop and mobile

Inspiration Style:
Think: 4x4 accessory brands, tough tradie gear, or clean eCommerce landing banners from premium auto suppliers.

Target Market(s)

All in Brief Above

Industry/Entity Type

Retail

Requirements
Must have
• A banner using our products only. A banner for each category, and 2 alternate banners for the home page.
Nice to have
• I have added some designs which i like..... Please take a look and take inspiration from them.

```html
<!DOCTYPE html>
<html lang="en">
<head>
<meta charset="utf-8">
<title>Kelvra Cargo Depot – Aluminium Canopies</title>
<link rel="stylesheet" href="https://fonts.googleapis.com/css2?family=Anton&display=swap">
<style>
  :root {
    --bg-dark: #1d2a31;
    --bg-mid: #34454e;
    --bg-light: #55666e;
    --headline: #ffffff;
    --accent: #ffd200;
    --cta: #a81e4b;
    --cta-text: #ffffff;
    --product-light: #e4e8ea;
    --product-mid: #a9b1b6;
  }
  html, body {
    margin: 0;
    padding: 0;
    width: 900px;
    height: 1200px;
    overflow: hidden;
  }
  .banner {
    position: relative;
    width: 900px;
    height: 1200px;
    overflow: hidden;
    background:
      radial-gradient(ellipse 420px 320px at 470px 640px, rgba(200,215,222,0.45), transparent 70%),
      radial-gradient(ellipse 520px 420px at 560px 300px, rgba(110,128,137,0.5), transparent 70%),
      radial-gradient(ellipse 600px 500px at 150px 900px, rgba(20,32,38,0.7), transparent 70%),
      linear-gradient(160deg, var(--bg-mid) 0%, var(--bg-dark) 55%, #15222a 100%);
    font-family: 'Anton', 'Impact', sans-serif;
  }
  .headline {
    position: absolute;
    left: 92px;
    top: 70px;
    margin: 0;
    color: var(--headline);
    font-size: 148px;
    line-height: 144px;
    font-weight: 400;
    letter-spacing: 1px;
    transform: scaleX(0.98);
    transform-origin: left;
  }
  .product-photo {
    position: absolute;
    left: 218px;
    top: 510px;
    width: 500px;
    height: 305px;
    background:
      radial-gradient(ellipse at 60% 55%, var(--product-light), var(--product-mid) 60%, rgba(169,177,182,0) 100%);
    border-radius: 30px;
  }
  .tagline {
    position: absolute;
    left: 96px;
    top: 818px;
    margin: 0;
    color: var(--accent);
    font-size: 73px;
    line-height: 82px;
    font-weight: 400;
    letter-spacing: 0.5px;
  }
  .cta {
    position: absolute;
    left: 92px;
    top: 1012px;
    width: 528px;
    height: 124px;
    border-radius: 22px;
    background: var(--cta);
    color: var(--cta-text);
    display: flex;
    align-items: center;
    justify-content: center;
    font-size: 76px;
    text-decoration: none;
    letter-spacing: 0.5px;
  }
</style>
</head>
<body>
  <main class="banner">
    <h1 class="headline">DURABLE<br>ALUMINIUM<br>CANOPIES</h1>
    <div class="product-photo" role="img" aria-label="Aluminium checker-plate ute canopy with gull-wing doors open and slide-out drawer"></div>
    <p class="tagline">SECURE AND SPACIOUS<br>SOLUTIONS FOR YOUR UTE</p>
    <a class="cta" href="https://www.kelvracargo.com.au/canopy/">EXPLORE</a>
  </main>
</body>
</html>
```